Einladungskarten-Design für Schützenverein
super gute Zusammenarbeit. Werde für weitere Arbeiten gerne darauf zurückkommen.
Zielgruppe
Wir sind ein Schützenverein und möchten mit einem neuzeitlichen Design für unser traditionelles Grümpelschiessen Werbung machen und die jüngere Generation für diesen schönen Sport begeistern.

```html
<!DOCTYPE html>
<html lang="de">
<head>
<meta charset="utf-8">
<title>Einladung zum Grümpelschiessen 2021</title>
<link href="https://fonts.googleapis.com/css2?family=Roboto:wght@400;500;700&display=swap" rel="stylesheet">
<style>
  :root {
    --club-blue: #26398f;
    --club-yellow: #f7dc17;
    --paper: #ffffff;
    --backdrop: #e4e4e4;
    --body-grey: #555a60;
    --photo-dark: #3c4a48;
    --photo-teal: #4f8f8c;
    --meadow: #7da65a;
  }
  * { margin: 0; padding: 0; box-sizing: border-box; }
  html, body {
    width: 1200px; height: 2256px; overflow: hidden;
    background: var(--backdrop);
    font-family: "Roboto", Arial, sans-serif;
  }
  .flyer {
    position: absolute; left: 50px; top: 350px;
    width: 1100px; height: 1556px;
    background: var(--paper);
    box-shadow: 0 4px 14px rgba(0,0,0,.18);
    overflow: hidden;
  }
  .flyer-shapes { position: absolute; inset: 0; }
  .abs { position: absolute; }

  .title-band {
    left: 60px; top: 76px; width: 811px; height: 102px;
    background: var(--club-blue); color: #fff;
    font-weight: 700; font-size: 66px; line-height: 102px;
    padding-left: 38px; letter-spacing: .5px;
  }
  .subtitle-band {
    left: 60px; top: 178px; width: 811px; height: 66px;
    background: var(--club-yellow); color: var(--club-blue);
    font-weight: 700; font-size: 41px; line-height: 66px;
    padding-left: 38px;
  }
  .club-mark {
    left: 871px; top: 76px; width: 168px; height: 168px;
    background: var(--club-blue);
    display: flex; flex-direction: column; justify-content: center;
    padding: 0 16px; gap: 12px;
  }
  .club-mark-square { width: 28px; height: 28px; background: var(--club-yellow); }
  .club-mark-name { color: #fff; font-weight: 700; font-size: 20px; line-height: 1.15; }

  .join-label {
    left: 291px; top: 1000px; width: 211px;
    text-align: center; color: #fff;
    font-weight: 700; font-size: 40px; line-height: 1.12;
  }

  .date-block { left: 595px; top: 870px; width: 430px; }
  .date-line { color: var(--club-yellow); font-weight: 700; font-size: 76px; line-height: 82px; }
  .venue { color: #fff; font-weight: 700; font-size: 29px; margin-top: 26px; }
  .parking { color: #fff; font-size: 20px; margin-top: 8px; }
  .info-strip {
    left: 568px; top: 1168px; width: 463px; height: 37px;
    background: var(--club-yellow); color: var(--club-blue);
    font-size: 19px; line-height: 37px; text-align: center;
  }
  .info-strip strong { font-weight: 500; }

  .facts-heading { color: var(--club-blue); font-weight: 700; font-size: 37px; line-height: 1.1; }
  .facts-text { color: var(--body-grey); font-size: 23px; line-height: 31px; margin-top: 6px; }
  .time-facts { left: 70px; top: 1128px; width: 420px; }
  .who-facts { left: 70px; top: 1228px; width: 420px; }
  .offer-facts { left: 568px; top: 1255px; width: 463px; }
  .offer-facts .facts-text { text-align: justify; text-align-last: left; }

  .closing-band {
    left: 0; top: 1412px; width: 1100px; height: 144px;
    background: var(--club-blue); color: var(--club-yellow);
    font-size: 26px; line-height: 42px; text-align: center;
    padding-top: 30px;
  }
  .closing-band em { font-weight: 700; }
</style>
</head>
<body>
<main class="flyer">
  <svg class="flyer-shapes" width="1100" height="1556" viewBox="0 0 1100 1556">
    <defs>
      <linearGradient id="rangeTones" x1="0" y1="0" x2="1" y2="1">
        <stop offset="0" stop-color="#8a8060"/>
        <stop offset=".35" stop-color="var(--photo-teal)"/>
        <stop offset=".7" stop-color="var(--photo-dark)"/>
        <stop offset="1" stop-color="#7c8288"/>
      </linearGradient>
      <linearGradient id="meadowTones" x1="0" y1="0" x2="0" y2="1">
        <stop offset="0" stop-color="#9cc07a"/>
        <stop offset="1" stop-color="#4d5a60"/>
      </linearGradient>
    </defs>
    <polygon points="0,0 1100,0 1100,620 0,1046" fill="url(#rangeTones)"
      role="img" aria-label="Foto: junge Schützin liegend am Schiessstand mit Gewehr und Trefferanzeige, daneben ein Betreuer"/>
    <polygon points="0,1046 1100,620 1100,642 0,1068" fill="var(--club-yellow)"/>
    <circle cx="199" cy="794" r="133" fill="url(#meadowTones)" stroke="#fff" stroke-width="4"
      role="img" aria-label="Foto: Blick vom Schützenhaus auf die grüne Schiessbahn"/>
    <polygon points="568,875 1031,697 1031,1168 568,1168" fill="var(--club-blue)"/>
    <polygon points="291,983 502,901 502,1109 291,1109" fill="var(--club-blue)"/>
  </svg>

  <div class="abs title-band">EINLADUNG ZUM</div>
  <div class="abs subtitle-band">GRÜMPELSCHIESSEN 2021 - FÜR ALLE</div>
  <div class="abs club-mark">
    <span class="club-mark-square"></span>
    <span class="club-mark-name">SCHÜTZENVEREIN TALBACH</span>
  </div>

  <div class="abs join-label">Machen<br>Sie mit!</div>

  <div class="abs date-block">
    <div class="date-line">Sonntag,<br>29. August</div>
    <div class="venue">Beim Schützenverein Talbach</div>
    <div class="parking">(Parkplätze bei der Talstation der Sonnhaldebahn)</div>
  </div>
  <div class="abs info-strip">Aktuelle Infos <strong>www.svtalbach.ch</strong></div>

  <section class="abs time-facts">
    <h2 class="facts-heading">Uhrzeit:</h2>
    <p class="facts-text">08.00 – 12.00 Uhr durchgehend</p>
  </section>
  <section class="abs who-facts">
    <h2 class="facts-heading">Wer:</h2>
    <p class="facts-text">Einzel, Paare und Familien &gt;<br>einfach jedermann ob jung ob alt<br>aus nah und fern, Frau und Mann</p>
  </section>
  <section class="abs offer-facts">
    <h2 class="facts-heading">Unser Angebot:</h2>
    <p class="facts-text">Grümpelstich und Festwirtschaft mit Mittagsmenü in herrlicher Umgebung</p>
  </section>

  <footer class="abs closing-band">
    Wir laden Sie herzlich zu einem gemütlichen Sonntag ein und<br>
    freuen uns auf Ihren Besuch und Ihre Teilnahme. <em>Ihr Schützenverein Talbach</em>
  </footer>
</main>
</body>
</html>
```